VANTOL GROUP

This is a company that provides executive protection. Our motto is "New Era in Protection"... I don't want this to look like other security websites. I want it to be clean and sharp and represent a new era. We are based in the bay area so maybe a picture of San Francisco in the background?
I want it to be able to funnel down a couple different categories.
1. About Us
2. Services (Executive Protection, Covert Protection, Residential Protection & Intelligence)
3. Blue Maple (Training & Consulting)
4. Contact Us
I want it to be very clean and modern. I don't want there to be any pictures of bodyguards with ear pieces like every other website.
Target Market(s)
Ultra High Net Worth Individuals
Coding
Coded - Design and coding required
Number of Pages Required
1 page
Requirements
Must have
- Colors of my Symbol
Nice to have
- City in the background, San Francisco, New York or the Pinecrest Lodge in Montana.
Should not have
- Should not look like an KVM website or have photos of bodyguards. I want this to be a clean and simple website with my logo

```html
<!DOCTYPE html>
<html lang="en">
<head>
<meta charset="utf-8">
<title>VANTOL GROUP — New Era in Protection</title>
<link href="https://fonts.googleapis.com/css2?family=Exo+2:wght@500;600;700&family=Michroma&family=Roboto:wght@400;500;700&display=swap" rel="stylesheet">
<style>
:root{
  --maroon:#7b0d14;
  --maroon-dark:#5e070c;
  --ink:#1b1b1b;
  --text:#555;
  --topbar:#1f1f1f;
  --header:#f6f6f6;
  --line:#dcdcdc;
  --footer:#1c1c1c;
}
*{box-sizing:border-box;margin:0;padding:0}
html,body{width:1200px;height:4125px;overflow:hidden}
body{position:relative;font-family:'Roboto',sans-serif;color:var(--ink);background:#fff}
.abs{position:absolute}
a{color:inherit;text-decoration:none}

/* top bar */
.topbar{left:0;top:0;width:1200px;height:54px;background:var(--topbar)}
.pill{position:absolute;top:8px;height:37px;border-radius:19px;font:500 17px 'Roboto',sans-serif;display:flex;align-items:center;justify-content:center}
.pill-login{left:90px;width:101px;background:#fff;color:var(--maroon)}
.pill-client{left:199px;width:118px;background:var(--maroon);color:#fff}
.lang{left:777px;top:17px;color:#fff;font:500 16px 'Roboto',sans-serif}
.social{display:flex;gap:16px}
.social span{width:32px;height:32px;border-radius:50%;background:var(--maroon);border:2px solid #fff}
.topbar .social{position:absolute;left:889px;top:11px}

/* header */
.header{left:0;top:54px;width:1200px;height:109px;background:var(--header)}
.logo{left:91px;top:26px;display:flex;align-items:center;gap:8px}
.logo-mark{width:22px;height:22px;background:var(--maroon)}
.logo-name{font:700 19px 'Exo 2',sans-serif;color:var(--ink);letter-spacing:1px;line-height:1.05}
.contact-icon{width:51px;height:51px;border-radius:50%;background:var(--maroon);display:flex;align-items:center;justify-content:center}
.contact-label{font:500 12px 'Roboto',sans-serif;color:var(--ink)}
.contact-value{font:500 15px 'Roboto',sans-serif;color:var(--ink);margin-top:6px}

/* nav */
.nav{left:0;top:163px;width:1200px;height:58px;background:#fff}
.nav a{position:absolute;top:23px;font:500 15px 'Roboto',sans-serif;color:#222}
.nav a.active{color:var(--maroon);text-decoration:underline}
.search{left:854px;top:7px;width:255px;height:43px;border:1px solid #ccc;border-radius:22px;padding-left:18px;font:italic 13px 'Roboto',sans-serif;color:#888;display:flex;align-items:center}
.search-btn{position:absolute;right:3px;top:3px;width:35px;height:35px;border-radius:50%;background:var(--maroon);display:flex;align-items:center;justify-content:center}

/* hero */
.hero{left:0;top:221px;width:1200px;height:630px;background:linear-gradient(180deg,#8fb3c6 0%,#d9b58d 35%,#5a6d78 60%,#2a4556 100%)}
.hero-title{left:88px;top:205px;font:400 60px 'Michroma',sans-serif;color:#fff;letter-spacing:2px}
.hero-sub{left:89px;top:283px;font:500 34px 'Exo 2',sans-serif;color:#fff}
.btn{display:flex;align-items:center;justify-content:center;border-radius:26px;font:500 17px 'Roboto',sans-serif}
.btn-maroon{background:var(--maroon);color:#fff}
.btn-white{background:#fff;color:var(--maroon)}
.dots span{position:absolute;top:592px;width:17px;height:17px;border-radius:50%;border:2px solid #fff}
.dots span.on{background:#fff}

/* section titles */
.section-title{width:1200px;left:0;text-align:center;font:700 42px 'Exo 2',sans-serif;color:var(--ink)}
.section-title.wide{font:400 40px 'Michroma',sans-serif;letter-spacing:1px}
.rule{left:588px;width:24px;height:4px;background:var(--maroon)}

/* services */
.svc-icon{width:88px;height:88px;border-radius:50%;border:1.5px solid #666;display:flex;align-items:center;justify-content:center}
.svc-title{font:600 23px 'Exo 2',sans-serif;color:var(--ink);letter-spacing:.3px}
.svc-text{width:390px;font:400 15.5px/26px 'Roboto',sans-serif;color:var(--text);margin-top:16px}

/* split */
.panel{top:1455px;width:600px;height:507px}
.panel-left{left:0;background:linear-gradient(135deg,#9a1520,#6d0a10)}
.panel-right{left:600px;background:linear-gradient(135deg,#6f7378,#3e4247 60%,#2a2d31)}
.panel h3{position:absolute;left:90px;top:90px;font:600 34px 'Exo 2',sans-serif;color:#fff}
.panel p{position:absolute;left:90px;width:475px;font:400 15.5px/26px 'Roboto',sans-serif;color:#fff}

/* testimonial */
.avatar{left:547px;top:2163px;width:107px;height:107px;border-radius:50%;background:linear-gradient(180deg,#c9c9c9,#8a8a8a)}
.quote{left:120px;top:2300px;width:960px;text-align:center;font:400 15.5px/34px 'Roboto',sans-serif;color:#333}
.quote-name{left:0;top:2388px;width:1200px;text-align:center;font:700 16px 'Roboto',sans-serif}
.arrow{font:400 28px 'Roboto',sans-serif;color:#444}

/* about */
.about-band{left:0;top:2525px;width:1200px;height:405px;background:linear-gradient(90deg,#b5a898 0%,#cfc9c1 30%,#8e9196 60%,#2b3036 80%,#1a1d22 100%)}
.about-card{left:288px;top:2624px;width:624px;height:396px;background:#fff;box-shadow:0 4px 14px rgba(0,0,0,.15)}
.about-card h2{position:absolute;left:0;top:50px;width:624px;text-align:center;font:700 42px 'Exo 2',sans-serif}
.about-card .rule{left:300px;top:116px}
.about-card p{position:absolute;left:22px;top:138px;width:580px;text-align:justify;text-align-last:center;font:400 15.5px/29px 'Roboto',sans-serif;color:var(--text)}

/* news */
.news-card{top:3209px;width:331px;height:418px;border:1.5px solid #d5d5d5;background:#fff}
.news-img{position:absolute;left:5px;top:4px;width:319px;height:196px}
.news-date{position:absolute;left:20px;top:166px;width:64px;height:61px;background:var(--maroon);color:#fff;text-align:center;font:500 20px/25px 'Roboto',sans-serif;padding-top:6px}
.news-title{position:absolute;left:20px;top:250px;width:300px;font:400 21px/25px 'Roboto',sans-serif;color:#222}
.news-text{position:absolute;left:21px;top:312px;width:290px;font:400 14px/22px 'Roboto',sans-serif;color:#444}
.news-more{position:absolute;left:21px;top:382px;font:500 15px 'Roboto',sans-serif;color:var(--maroon)}

/* footer */
.footer{left:0;top:3730px;width:1200px;height:395px;background:var(--footer);color:#fff}
.footer h4{position:absolute;top:104px;font:600 23px 'Exo 2',sans-serif}
.footer .col{position:absolute;top:158px;font:400 13.5px/20px 'Roboto',sans-serif;color:#ddd}
.footer .vline{position:absolute;top:105px;width:1px;height:180px;background:#444}
.newsletter-input{position:absolute;left:830px;top:209px;width:243px;height:40px;background:#fff;font:400 11px 'Roboto',sans-serif;color:#999;padding:14px 14px}
.newsletter-btn{position:absolute;left:1073px;top:209px;width:40px;height:40px;background:var(--maroon);display:flex;align-items:center;justify-content:center}
.footer .social{position:absolute;left:830px;top:278px;gap:15px}
.footer .social span{width:32px;height:32px;border:none}
.copyright{position:absolute;left:0;top:362px;width:1200px;text-align:center;font:400 11px 'Roboto',sans-serif;color:#eee}
</style>
</head>
<body>

<!-- top bar -->
<div class="abs topbar">
  <a class="pill pill-login">Login</a>
  <a class="pill pill-client">Client</a>
  <div class="abs lang">EN &#8964;</div>
  <div class="social"><span></span><span></span><span></span><span></span><span></span></div>
</div>

<!-- header -->
<header class="abs header">
  <div class="abs logo"><span class="logo-mark"></span><span class="logo-name">VANTOL<br>GROUP</span></div>
  <div class="abs contact-icon" style="left:628px;top:29px">
    <svg width="20" height="20" viewBox="0 0 24 24"><path fill="#fff" d="M6.6 10.8a15 15 0 0 0 6.6 6.6l2.2-2.2c.3-.3.7-.4 1-.2 1.1.4 2.3.6 3.6.6.6 0 1 .4 1 1V20c0 .6-.4 1-1 1C10.6 21 3 13.4 3 4c0-.6.4-1 1-1h3.5c.6 0 1 .4 1 1 0 1.3.2 2.5.6 3.6.1.3 0 .7-.2 1z"/></svg>
  </div>
  <div class="abs" style="left:695px;top:36px"><div class="contact-label">CALL &nbsp;US :</div><div class="contact-value">+1 555 010 2152</div></div>
  <div class="abs contact-icon" style="left:912px;top:29px">
    <svg width="20" height="16" viewBox="0 0 24 18"><path fill="#fff" d="M0 0h24v2L12 10 0 2z"/><path fill="#fff" d="M0 5l12 8 12-8v13H0z"/></svg>
  </div>
  <div class="abs" style="left:979px;top:36px"><div class="contact-label">EMAIL :</div><div class="contact-value">hello@vantolgroup.com</div></div>
</header>

<!-- nav -->
<nav class="abs nav">
  <a class="active" style="left:90px">HOME</a>
  <a style="left:189px">ABOUT US</a>
  <a style="left:317px">SERVICES</a>
  <a style="left:441px">BLUE MAPLE</a>
  <a style="left:580px">CONTACT US</a>
  <div class="abs search">Enter a &nbsp;Keyword
    <span class="search-btn"><svg width="14" height="14" viewBox="0 0 16 16"><circle cx="6.5" cy="6.5" r="4.5" fill="none" stroke="#fff" stroke-width="2"/><path d="M10 10l4 4" stroke="#fff" stroke-width="2"/></svg></span>
  </div>
</nav>

<!-- hero -->
<section class="abs hero" role="img" aria-label="San Francisco skyline and Bay Bridge at sunset over the water">
  <h1 class="abs hero-title">VANTOL GROUP</h1>
  <p class="abs hero-sub">New Era in Protection</p>
  <a class="abs btn btn-maroon" style="left:91px;top:359px;width:194px;height:50px">Get Started</a>
  <div class="dots"><span class="on" style="left:541px"></span><span style="left:574px"></span><span style="left:608px"></span><span style="left:641px"></span></div>
</section>

<!-- services -->
<h2 class="abs section-title wide" style="top:940px">OUR SERVICES</h2>
<div class="abs rule" style="top:1002px"></div>

<div class="abs svc-icon" style="left:85px;top:1050px">
  <svg width="48" height="48" viewBox="0 0 48 48" fill="none" stroke="var(--maroon)" stroke-width="2"><rect x="6" y="10" width="28" height="20"/><path d="M2 34h36"/><path d="M36 18l8 3v7c0 5-4 8-8 10-4-2-8-5-8-10v-7z"/></svg>
</div>
<div class="abs" style="left:187px;top:1046px"><div class="svc-title">EXECUTIVE PROTECTION</div><p class="svc-text">Lorem ipsum dolor sit amet, consectetur adipiscing elit, sed do eiusmod tempor incididunt ut labore et dolore magna aliqua.</p></div>

<div class="abs svc-icon" style="left:641px;top:1050px">
  <svg width="48" height="48" viewBox="0 0 48 48" fill="none" stroke="var(--maroon)" stroke-width="2"><rect x="13" y="22" width="22" height="18" rx="2"/><path d="M17 22v-6a7 7 0 0 1 14 0v6"/><circle cx="24" cy="30" r="2"/><path d="M24 32v4"/></svg>
</div>
<div class="abs" style="left:747px;top:1046px"><div class="svc-title">COVERT PROTECTION</div><p class="svc-text">Lorem ipsum dolor sit amet, consectetur adipiscing elit, sed do eiusmod tempor incididunt ut labore et dolore magna aliqua.</p></div>

<div class="abs svc-icon" style="left:85px;top:1241px">
  <svg width="48" height="48" viewBox="0 0 48 48" fill="none" stroke="var(--maroon)" stroke-width="2"><path d="M6 24L22 10l16 14"/><path d="M10 21v19h24V21"/><rect x="18" y="28" width="8" height="12"/></svg>
</div>
<div class="abs" style="left:187px;top:1237px"><div class="svc-title">RESIDENTIAL PROTECTION</div><p class="svc-text">Lorem ipsum dolor sit amet, consectetur adipiscing elit, sed do eiusmod tempor incididunt ut labore et dolore magna aliqua.</p></div>

<div class="abs svc-icon" style="left:641px;top:1241px">
  <svg width="48" height="48" viewBox="0 0 48 48" fill="none" stroke="var(--maroon)" stroke-width="2"><rect x="14" y="14" width="20" height="20" rx="2"/><path d="M19 8v6M24 8v6M29 8v6M19 34v6M24 34v6M29 34v6M8 19h6M8 24h6M8 29h6M34 19h6M34 24h6M34 29h6"/></svg>
</div>
<div class="abs" style="left:747px;top:1237px"><div class="svc-title">INTELLIGENCE</div><p class="svc-text">Lorem ipsum dolor sit amet, consectetur adipiscing elit, sed do eiusmod tempor incididunt ut labore et dolore magna aliqua.</p></div>

<!-- training / consulting -->
<section class="abs panel panel-left" role="img" aria-label="Red-toned image of padlocks, training theme">
  <h3>Training</h3>
  <p style="top:153px">Lorem ipsum dolor sit amet, consectetur adipiscing elit, sed do eiusmod tempor incididunt ut labore et dolore magna aliqua.</p>
  <p style="top:219px">Lorem ipsum dolor sit amet, consectetur adipiscing elit, sed do eiusmod tempor incididunt ut labore et dolore magna aliqua. Ut enim ad minim veniam, quis nostrud exercitation ullamco laboris nisi ut aliquip ex ea commodo consequat.</p>
  <a class="abs btn btn-white" style="left:91px;top:358px;width:157px;height:49px">Read More</a>
</section>
<section class="abs panel panel-right" role="img" aria-label="Analyst working at a desk with monitors, consulting theme">
  <h3 style="left:54px">Consulting</h3>
  <p style="left:55px;top:153px">Lorem ipsum dolor sit amet, consectetur adipiscing elit, sed do eiusmod tempor incididunt ut labore et dolore magna aliqua.</p>
  <p style="left:55px;top:219px">Lorem ipsum dolor sit amet, consectetur adipiscing elit, sed do eiusmod tempor incididunt ut labore et dolore magna aliqua. Ut enim ad minim veniam, quis nostrud exercitation ullamco laboris nisi ut aliquip ex ea commodo consequat.</p>
  <a class="abs btn btn-maroon" style="left:56px;top:358px;width:157px;height:49px">Read More</a>
</section>

<!-- testimonials -->
<h2 class="abs section-title" style="top:2052px">Testimonials</h2>
<div class="abs rule" style="top:2115px"></div>
<div class="abs avatar" role="img" aria-label="Portrait of the client giving the testimonial"></div>
<div class="abs arrow" style="left:36px;top:2270px">&#8249;</div>
<div class="abs arrow" style="left:1148px;top:2270px">&#8250;</div>
<p class="abs quote">Lorem ipsum dolor sit amet, consectetur adipiscing elit, sed do eiusmod tempor incididunt ut labore et dolore magna aliqua. Ut enim ad minim veniam, quis nostrud exercitation ullamco laboris nisi ut aliquip ex ea commodo consequat.</p>
<p class="abs quote-name">-Dana Whitfield</p>

<!-- about -->
<div class="abs about-band" role="img" aria-label="Office desk with coffee cup and a laptop showing a green padlock over code"></div>
<section class="abs about-card">
  <h2>About Us</h2>
  <div class="abs rule"></div>
  <p>Lorem ipsum dolor sit amet, consectetur adipiscing elit, sed do eiusmod tempor incididunt ut labore et dolore magna aliqua. Ut enim ad minim veniam, quis nostrud exercitation ullamco laboris nisi ut aliquip ex ea commodo consequat. Duis aute irure dolor in reprehenderit in voluptate velit esse cillum dolore eu fugiat nulla pariatur. Excepteur sint occaecat cupidatat non proident</p>
  <a class="abs btn btn-maroon" style="left:234px;top:300px;width:157px;height:49px">Read More</a>
</section>

<!-- news -->
<h2 class="abs section-title" style="top:3108px">News</h2>
<div class="abs rule" style="top:3171px"></div>
<div class="abs arrow" style="left:38px;top:3364px">&#8249;</div>
<div class="abs arrow" style="left:1146px;top:3364px">&#8250;</div>

<article class="abs news-card" style="left:91px">
  <div class="news-img" role="img" aria-label="Digital head with glowing data network" style="background:linear-gradient(135deg,#1b2b5a,#3a6fb5 55%,#0d1630)"></div>
  <div class="news-date">25<br>FEB</div>
  <div class="news-title">Lorem ipsum dolor sit amet, consectetur adipiscing</div>
  <div class="news-text">Lorem ipsum dolor sit amet, consect etur adipiscing elit, sed do eiusmtempor incididunt ut labore et dolore</div>
  <a class="news-more">Read More</a>
</article>
<article class="abs news-card" style="left:434px">
  <div class="news-img" role="img" aria-label="Hands holding a glowing network globe" style="background:linear-gradient(135deg,#9aa6b4,#4d6690 50%,#1f2a44)"></div>
  <div class="news-date">25<br>FEB</div>
  <div class="news-title">Lorem ipsum dolor sit amet, consectetur adipiscing</div>
  <div class="news-text">Lorem ipsum dolor sit amet, consect etur adipiscing elit, sed do eiusmtempor incididunt ut labore et dolore</div>
  <a class="news-more">Read More</a>
</article>
<article class="abs news-card" style="left:779px">
  <div class="news-img" role="img" aria-label="Security camera outside a lit house at dusk" style="background:linear-gradient(135deg,#5e5a55,#b39a76 45%,#2c2c2e)"></div>
  <div class="news-date">25<br>FEB</div>
  <div class="news-title">Lorem ipsum dolor sit amet, consectetur adipiscing</div>
  <div class="news-text">Lorem ipsum dolor sit amet, consect etur adipiscing elit, sed do eiusmtempor incididunt ut labore et dolore</div>
  <a class="news-more">Read More</a>
</article>

<!-- footer -->
<footer class="abs footer">
  <h4 style="left:88px">Contact Us</h4>
  <div class="col" style="left:89px">COMPANY<br>18 Harbor Street, NY 10012<br><br>EMAIL ADDRESS<br>hello@vantolgroup.com<br><br>CALL US<br>+1 555 014 6542</div>
  <span class="vline" style="left:372px"></span>
  <h4 style="left:421px">Links</h4>
  <div class="col" style="left:423px;line-height:27px;top:152px">Home<br>About Us<br>Services<br>Blue Maple<br>Contact Us</div>
  <span class="vline" style="left:580px"></span>
  <h4 style="left:641px">Legal</h4>
  <div class="col" style="left:643px;line-height:27px;top:152px">Support<br>Faq<br>Sitemap<br>Contact Us</div>
  <span class="vline" style="left:766px"></span>
  <h4 style="left:828px">Newsletter</h4>
  <div class="col" style="left:830px">For exclusive news and updates sign up<br>for our newsletter.</div>
  <div class="newsletter-input">Email Address</div>
  <div class="newsletter-btn"><svg width="16" height="16" viewBox="0 0 16 16"><path d="M1 7l14-6-5 14-2-6z" fill="none" stroke="#fff" stroke-width="1.4"/></svg></div>
  <div class="social"><span></span><span></span><span></span><span></span><span></span></div>
  <p class="copyright">© 2021 Copyrights.THE COMPANY NAME.All Rights Reserved | Privacy Policy, Terms of Service</p>
</footer>

</body>
</html>
```